we need an experienced designer to design the tube for our toothpaste

Design guidelines:
1. On the front side, our product logo (‘K7320’) should be prominent enough.
2. Our brand logo (‘lumbrisk’) could be small-size and it's just a trademark indeed.

Some information here for your reference:
1. The color of toothpaste cap is white.
2. We hope that the primary color in the design is blue.
3.‘F’ in ‘K7320’ stands for ‘lumbrisk’ and ‘fluoride’.
4. We will use aluminum-plastic composite materials to make toothpaste tubes. In addition to the design, we also hope that you can make relevant suggestions on the special requirements of printing.

At last, we hope that you could submit both 2D design and 3D visual effects.

Attachments:
Product logo: K7320
Brand logo: lumbrisk
illustration ONE: metal braces
illustration TWO: clear aligners

Colors
0094D4
00A9DD
6FCCEA
C7EBF8
E9F6FB

Requirements
Must have
• as attached

```html
<!DOCTYPE html>
<html lang="en">
<head>
<meta charset="utf-8">
<title>K7320 Orthodontic Toothpaste – Tube Artwork</title>
<link rel="stylesheet" href="https://fonts.googleapis.com/css2?family=Exo+2:ital,wght@1,500&family=Fira+Sans+Condensed:wght@400;500;700;800&family=Fira+Sans:ital,wght@0,400;0,600;1,800&family=Rubik:wght@800&display=swap">
<style>
  :root {
    --blue-deep: #3f6eab;
    --blue-mid: #5a83bd;
    --blue-soft: #86a5d0;
    --blue-text: #3a66a6;
    --blue-muted: #6f8fc2;
    --white: #ffffff;
    --cap: #f1f2f4;
    --page: #ffffff;
    --gum: #e7a0a6;
    --skin: #f2d3c8;
  }
  * { margin: 0; padding: 0; box-sizing: border-box; }
  html, body { width: 1200px; height: 960px; overflow: hidden; background: var(--page); }
  .canvas { position: relative; width: 1200px; height: 960px; }
  .tube { position: absolute; left: 0; width: 1200px; height: 300px; }
  .tube--front { top: 190px; }
  .tube--back { top: 510px; }
  .tube-shape { position: absolute; inset: 0; }
  .tube-text { position: absolute; }

  .brand-name {
    left: 254px; top: 30px;
    font: 700 22px "Fira Sans Condensed", sans-serif;
    color: var(--blue-text);
    display: flex; align-items: center; gap: 6px;
  }
  .brand-dot { width: 9px; height: 9px; border-radius: 50%; background: var(--blue-text); }
  .product-name {
    left: 248px; top: 88px;
    font: 800 92px/1 "Rubik", sans-serif;
    color: var(--blue-mid);
    letter-spacing: 2px;
  }
  .product-type {
    left: 254px; top: 188px;
    font: 700 10px "Fira Sans", sans-serif;
    color: var(--blue-muted);
  }
  .product-claims {
    left: 254px; top: 205px;
    font: italic 500 9.6px/1.45 "Exo 2", sans-serif;
    color: var(--blue-muted);
    letter-spacing: 0.4px;
  }
  .product-claims .strong { color: var(--blue-text); }
  .fluoride {
    right: 125px; top: 22px;
    text-align: right;
    font: italic 800 40px/1.1 "Fira Sans", sans-serif;
    color: var(--white);
  }
  .flavour {
    right: 125px; top: 186px;
    font: 400 25px "Fira Sans Condensed", sans-serif;
    color: var(--white);
  }
  .net-weight {
    right: 125px; top: 224px;
    font: 400 17px "Fira Sans Condensed", sans-serif;
    color: var(--white);
  }

  .usage {
    left: 254px; top: 72px; width: 400px;
    font: 400 10.4px/1.4 "Fira Sans", sans-serif;
    color: var(--blue-text);
  }
  .usage h3 { font-weight: 600; font-size: 10.6px; margin-top: 8px; }
  .usage h3:first-child { margin-top: 0; }
  .usage .light { color: var(--blue-muted); }

  .care-title {
    left: 1010px; top: 42px; height: 230px;
    writing-mode: vertical-rl;
    font: 800 19px/1.05 "Fira Sans Condensed", sans-serif;
    color: var(--white);
  }
  .benefits {
    left: 872px; top: 52px; height: 220px;
    writing-mode: vertical-rl;
    font: 500 10px/1.5 "Fira Sans Condensed", sans-serif;
    color: var(--white);
  }
  .benefits li { list-style: none; display: inline; margin-bottom: 10px; }
  .benefits .tick { font-size: 8px; }
  .ortho-illustration { position: absolute; left: 924px; width: 64px; }
  .ortho-illustration--aligner { top: 42px; height: 100px; background: linear-gradient(90deg, var(--gum), var(--skin)); }
  .ortho-illustration--braces { top: 154px; height: 100px; background: linear-gradient(90deg, var(--gum), var(--skin)); }
</style>
</head>
<body>
<main class="canvas">

  <section class="tube tube--front" aria-label="Tube front">
    <svg class="tube-shape" width="1200" height="300" viewBox="0 0 1200 300">
      <defs>
        <linearGradient id="bandFront" x1="0" y1="1" x2="1" y2="0">
          <stop offset="0" stop-color="var(--blue-soft)"/>
          <stop offset="0.5" stop-color="var(--blue-mid)"/>
          <stop offset="1" stop-color="var(--blue-deep)"/>
        </linearGradient>
      </defs>
      <rect x="92" y="100" width="100" height="100" rx="4" fill="var(--cap)" stroke="#dcdfe3"/>
      <path d="M190 95 L232 12 L232 283 L190 205 Z" fill="#f6f7f8"/>
      <rect x="228" y="12" width="880" height="271" fill="var(--white)" stroke="#eef0f2"/>
      <path d="M745 12 C700 80 790 140 725 200 C690 240 770 262 730 283 L1104 283 L1104 12 Z" fill="url(#bandFront)"/>
      <rect x="1100" y="8" width="42" height="279" fill="var(--blue-mid)"/>
      <g stroke="#7e9ccb" stroke-width="1">
        <line x1="1100" y1="20" x2="1142" y2="20"/><line x1="1100" y1="40" x2="1142" y2="40"/>
        <line x1="1100" y1="60" x2="1142" y2="60"/><line x1="1100" y1="80" x2="1142" y2="80"/>
        <line x1="1100" y1="100" x2="1142" y2="100"/><line x1="1100" y1="120" x2="1142" y2="120"/>
        <line x1="1100" y1="140" x2="1142" y2="140"/><line x1="1100" y1="160" x2="1142" y2="160"/>
        <line x1="1100" y1="180" x2="1142" y2="180"/><line x1="1100" y1="200" x2="1142" y2="200"/>
        <line x1="1100" y1="220" x2="1142" y2="220"/><line x1="1100" y1="240" x2="1142" y2="240"/>
        <line x1="1100" y1="260" x2="1142" y2="260"/><line x1="1100" y1="280" x2="1142" y2="280"/>
      </g>
    </svg>
    <div class="tube-text brand-name">lumbrisk<span class="brand-dot"></span></div>
    <div class="tube-text product-name">K7320</div>
    <div class="tube-text product-type">ORTHODONTIC TOOTHPASTE</div>
    <div class="tube-text product-claims">
      ENHANCED CAVITY PREVENTION AND GUM PROTECTION<br>
      <span class="strong">FOR USE WHEN WEARING METAL BRACES AND CLEAR ALIGNERS</span>
    </div>
    <div class="tube-text fluoride">Fluoride<br>1450 ppm</div>
    <div class="tube-text flavour">Double Mint</div>
    <div class="tube-text net-weight">NET WT. 85g</div>
  </section>

  <section class="tube tube--back" aria-label="Tube back">
    <svg class="tube-shape" width="1200" height="300" viewBox="0 0 1200 300">
      <defs>
        <linearGradient id="bandBack" x1="0" y1="1" x2="1" y2="0">
          <stop offset="0" stop-color="var(--blue-soft)"/>
          <stop offset="0.5" stop-color="var(--blue-mid)"/>
          <stop offset="1" stop-color="var(--blue-deep)"/>
        </linearGradient>
      </defs>
      <rect x="92" y="100" width="100" height="100" rx="4" fill="var(--cap)" stroke="#dcdfe3"/>
      <path d="M190 95 L232 12 L232 283 L190 205 Z" fill="#f6f7f8"/>
      <rect x="228" y="12" width="880" height="271" fill="var(--white)" stroke="#eef0f2"/>
      <path d="M740 12 C640 60 680 160 730 180 C770 220 700 250 760 283 L1104 283 L1104 12 Z" fill="url(#bandBack)"/>
      <rect x="1100" y="8" width="42" height="279" fill="var(--blue-mid)"/>
      <g stroke="#7e9ccb" stroke-width="1">
        <line x1="1100" y1="20" x2="1142" y2="20"/><line x1="1100" y1="40" x2="1142" y2="40"/>
        <line x1="1100" y1="60" x2="1142" y2="60"/><line x1="1100" y1="80" x2="1142" y2="80"/>
        <line x1="1100" y1="100" x2="1142" y2="100"/><line x1="1100" y1="120" x2="1142" y2="120"/>
        <line x1="1100" y1="140" x2="1142" y2="140"/><line x1="1100" y1="160" x2="1142" y2="160"/>
        <line x1="1100" y1="180" x2="1142" y2="180"/><line x1="1100" y1="200" x2="1142" y2="200"/>
        <line x1="1100" y1="220" x2="1142" y2="220"/><line x1="1100" y1="240" x2="1142" y2="240"/>
        <line x1="1100" y1="260" x2="1142" y2="260"/><line x1="1100" y1="280" x2="1142" y2="280"/>
      </g>
    </svg>
    <div class="tube-text usage">
      <h3>Directions</h3>
      <p>Apply at least one inch strip of the product onto a soft bristle toothbrush.<br>Brush teeth thoroughly, for at least three minutes twice a day.</p>
      <h3>Ingredients:</h3>
      <p>Aqua, Sorbitol, Hydrated Silica, Glycerin, PEG-12, Sodium Lauryl Sulfate,<br>Aroma, Cellulose Gum, Titanium Dioxide, Potassium Sorbate, Allantoin,<br><span class="light">Sodium Fluoride, Citric Acid, Peppermint Essence, Sodium Saccharin,<br>CI 47005, CI 42090, Cinnamal.</span></p>
      <h3>Warnings:</h3>
      <p class="light">Do not ingest. Keep out of reach of children under 6 years of age.</p>
    </div>
    <div class="ortho-illustration ortho-illustration--aligner" role="img" aria-label="Illustration of teeth wearing a clear aligner"></div>
    <div class="ortho-illustration ortho-illustration--braces" role="img" aria-label="Illustration of teeth wearing metal braces"></div>
    <ul class="tube-text benefits">
      <li><span class="tick">✓</span>PREVENT CAVITY &nbsp;<span class="tick">✓</span>FRESHEN BREATH</li><br>
      <li><span class="tick">✓</span>STRENGTHEN TEETH</li>
    </ul>
    <div class="tube-text care-title">PREMIUM ORAL CARE<br>DURING ORTHODONTIC<br>TREATMENT</div>
  </section>

</main>
</body>
</html>
```